Brightwave Exterior cleaning Logo

We need a new business card design, i would like to use our existing logo (attached).
Our logo on the left & a unique graphic design on the right of either a man holding a pressure washer gun & hose with a thumbs up or an image portraying dirt melting off a building or the two incorperated together, or something similar that represents exterior cleaning in progress, an image that shows/explains that we are exterior cleaners/pressure washers. Has to incorporate the zentrix & chatlane symbol perhaps in the bottom corners of the business card.
Existing business symbol on the back of the card with some blank lines for space to hand write quotes or job notes.
Industry/Entity Type
Exterior Cleaning
Contact Information for Business Card
Business mobile No. to be prominent (0472 918 346) Services provided listed as dot points. -Soft Washing -Pressure Washing - Solar Panel Cleaning - All General Exterior Cleaning. Email listed in fineprint (enquiries@tallowbrookwashworks.com.au). Owner Operator - Declan Morrow (this should also be added somewhere prominent). Residential & Comercial Cleaning.
Colors
Designer to choose colors to be used in the design.
Look and feel

```html
<!DOCTYPE html>
<html lang="en">
<head>
<meta charset="utf-8">
<title>Tallowbrook Washworks – Business Card</title>
<link rel="stylesheet" href="https://fonts.googleapis.com/css2?family=Roboto:wght@400;500;700&display=swap">
<style>
  :root {
    --backdrop: #3a3a3b;
    --card: #141416;
    --card-edge: #4a62b0;
    --brand-blue: #4a62b0;
    --text-light: #e9e9ec;
    --pattern-dark: #050506;
    --pattern-mid: #1c1c1f;
    --pattern-light: #404044;
  }
  * { box-sizing: border-box; margin: 0; padding: 0; }
  html, body {
    width: 1200px; height: 801px; overflow: hidden;
    background: var(--backdrop);
    font-family: "Roboto", Arial, sans-serif;
  }
  .canvas {
    position: relative; width: 1200px; height: 801px;
    display: flex; align-items: center; justify-content: center; gap: 40px;
  }
  .card {
    position: relative; width: 540px; height: 310px;
    background: var(--card);
    border-radius: 16px;
    border: 1.5px solid var(--card-edge);
    overflow: hidden;
  }
  /* Front */
  .brand {
    position: absolute; left: 30px; top: 70px; width: 196px;
    display: flex; flex-direction: column; gap: 12px;
  }
  .brand-mark { width: 44px; height: 44px; background: var(--brand-blue); }
  .brand-name {
    color: var(--text-light);
    font-weight: 500; font-size: 24px; line-height: 1.15; letter-spacing: 0.5px;
    text-transform: uppercase;
  }
  .divider {
    position: absolute; left: 238px; top: 58px; width: 1px; height: 150px;
    background: var(--brand-blue);
  }
  .details { position: absolute; left: 262px; top: 52px; right: 16px; }
  .owner-name {
    color: var(--brand-blue); font-weight: 700; font-size: 22px;
    text-transform: uppercase; letter-spacing: 0.2px;
  }
  .owner-role { color: var(--text-light); font-size: 13px; margin: 2px 0 12px; }
  .contact-list { list-style: none; }
  .contact-list li {
    display: flex; align-items: center; gap: 6px;
    color: var(--text-light); font-size: 11.5px; line-height: 1.7; white-space: nowrap;
  }
  .contact-list li.phone { color: var(--brand-blue); font-weight: 700; font-size: 14px; }
  .contact-list svg { width: 11px; height: 11px; flex: none; fill: var(--text-light); }
  .contact-list li.phone svg { fill: var(--brand-blue); }
  .sectors { color: var(--text-light); font-size: 12.5px; margin-top: 12px; }
  .services {
    position: absolute; left: 24px; right: 16px; bottom: 22px;
    color: var(--text-light); font-size: 12.5px; white-space: nowrap;
  }
  .services .dot { color: var(--brand-blue); margin: 0 4px; }
  /* Back */
  .pattern-area {
    position: absolute; inset: 0;
    background:
      radial-gradient(ellipse at 85% 15%, rgba(90,90,96,0.55) 0%, rgba(90,90,96,0) 55%),
      linear-gradient(120deg, var(--pattern-dark) 0%, var(--pattern-mid) 45%, var(--pattern-light) 100%);
  }
  .back-brand {
    position: absolute; left: 300px; top: 168px;
    display: flex; align-items: center; gap: 10px;
  }
  .back-brand .brand-mark { width: 30px; height: 30px; }
  .back-brand .brand-name { font-size: 15px; }
</style>
</head>
<body>
<main class="canvas">
  <section class="card card-front">
    <div class="brand">
      <span class="brand-mark"></span>
      <span class="brand-name">Tallowbrook Washworks</span>
    </div>
    <div class="divider"></div>
    <div class="details">
      <h1 class="owner-name">Declan Morrow</h1>
      <p class="owner-role">Owner Operator</p>
      <ul class="contact-list">
        <li class="phone">
          <svg viewBox="0 0 24 24"><path d="M6.6 10.8a15.1 15.1 0 0 0 6.6 6.6l2.2-2.2a1 1 0 0 1 1-.25 11.4 11.4 0 0 0 3.6.57 1 1 0 0 1 1 1V20a1 1 0 0 1-1 1A17 17 0 0 1 3 4a1 1 0 0 1 1-1h3.5a1 1 0 0 1 1 1c0 1.25.2 2.45.57 3.57a1 1 0 0 1-.25 1z"/></svg>
          0472 918 346
        </li>
        <li>
          <svg viewBox="0 0 24 24"><path d="M2 5h20v14H2z M2 5l10 8 10-8" fill="none" stroke="#e9e9ec" stroke-width="2"/></svg>
          enquiries@tallowbrookwashworks.com.au
        </li>
        <li>
          <svg viewBox="0 0 24 24"><circle cx="12" cy="12" r="9" fill="none" stroke="#e9e9ec" stroke-width="2"/><path d="M3 12h18M12 3c3 3 3 15 0 18M12 3c-3 3-3 15 0 18" fill="none" stroke="#e9e9ec" stroke-width="1.6"/></svg>
          www.tallowbrookwashworks.com.au
        </li>
      </ul>
      <p class="sectors">Residential &amp; Comercial Cleaning</p>
    </div>
    <p class="services">Soft Washing<span class="dot">•</span>Pressure Washing<span class="dot">•</span>Solar Panel Cleaning<span class="dot">•</span>All General Exterior Cleaning</p>
  </section>

  <section class="card card-back">
    <div class="pattern-area" role="img" aria-label="Repeating pattern of black and grey slanted diamond tiles fading from dark to light"></div>
    <div class="back-brand">
      <span class="brand-mark"></span>
      <span class="brand-name">Tallowbrook Washworks</span>
    </div>
  </section>
</main>
</body>
</html>
```